Brochure for a website accessibility report

This brochure is related to a report that www.qelvantrix.org sell. The report shows the results of an automated audit of a websites accessibility. It shows details of issues found with screen shots, examples of code and provides remediation advice.

The brochure will be a pdf 8.5 inches by 11 inches. It can be anywhere from 6 to 10 pages.

The FlintVue™ name itself should be “Bree Serif” font. The fonts, styles, colors and sizes are up to you.

The images used and logo of the Office of Digital Reachworks and K7P logo are upload

We highlighted in blue page extracts from the report we sell. Do not use the blue highlight, it is merely there to show you where the specific examples of the report we sell are vs the other content in the report. The areas in blue which show the content from the actual report should be shown as an extract of the actual page of the report. You have flexibility to change the layout and the way the content look.

The red square callouts over the blue content are callouts that describe the specific page extracts. We used it as a red callout only so that you would be able to see it. You should change the specific location, look and feel of the callout to be appropriate

Target Market(s)

Marketing and Technical people

Industry/Entity Type

Information Technology

Font styles to use
Sans Serif

Colors

Designer to choose colors to be used in the design.

Requirements
Should not have
• wheelchairs, images of blind people

```html
<!DOCTYPE html>
<html lang="en">
<head>
<meta charset="utf-8">
<title>FlintVue™ Accessibility Report – WCAG Principles</title>
<link href="https://fonts.googleapis.com/css2?family=Bree+Serif&family=Roboto:wght@300;400;500&display=swap" rel="stylesheet">
<style>
  :root{
    --page:#f8f5f1;
    --card:#fdf1e1;
    --panel:#ffffff;
    --green:#27a86b;
    --label:#e8c48e;
    --intro:#2f4d3c;
    --body:#4a4a4a;
    --strong:#111111;
    --logo-blue:#1f5c99;
    --bullet:#e8c48e;
  }
  *{margin:0;padding:0;box-sizing:border-box}
  html,body{width:928px;height:1200px;overflow:hidden;background:var(--page)}
  body{font-family:"Roboto",Arial,sans-serif;color:var(--body);position:relative}
  .lead{position:absolute;left:52px;top:80px;width:824px;font-weight:300;font-size:16.4px;line-height:20px;text-align:justify;color:#555}
  .standards-mark{position:absolute;left:52px;top:210px;display:flex;align-items:center;gap:10px}
  .standards-mark .square{width:30px;height:30px;background:var(--logo-blue)}
  .standards-mark .name{font-size:30px;font-weight:500;color:var(--logo-blue);letter-spacing:1px}
  .scope{position:absolute;left:52px;top:276px;font-size:16.6px;font-weight:300;color:var(--intro)}
  .principle{position:absolute;background:var(--card);border-radius:24px;padding:28px 32px 0 32px;box-shadow:0 6px 14px rgba(0,0,0,.07)}
  .principle .tag{font-size:12.5px;color:var(--label);text-transform:uppercase;margin-bottom:6px}
  .principle .tag b{font-weight:500}
  .principle h2{font-family:"Bree Serif",Georgia,serif;font-weight:400;font-size:31px;color:var(--green);line-height:1.1;margin-bottom:12px}
  .principle p{font-size:14.6px;line-height:18px;font-weight:400;color:#444}
  .principle p.key{margin-top:10px;font-weight:500;color:var(--strong)}
  .p1{left:52px;top:328px;width:396px;height:218px}
  .p2{left:480px;top:328px;width:396px;height:206px}
  .p3{left:52px;top:580px;width:396px;height:208px}
  .p4{left:481px;top:568px;width:395px;height:220px}
  .report-panel{position:absolute;left:52px;top:838px;width:876px;height:362px;background:var(--panel);border-top-left-radius:64px;padding:50px 52px 0 50px}
  .report-panel .pitch{font-size:16.6px;font-weight:300;line-height:20px;text-align:justify;color:#555}
  .report-panel .overview{margin-top:22px;font-size:14.6px;font-weight:300;line-height:18.5px;text-align:justify;color:#555}
  .report-panel ul{list-style:none;margin-top:22px}
  .report-panel li{position:relative;padding-left:32px;font-size:14.6px;font-weight:300;line-height:18.5px;text-align:justify;color:#555;margin-bottom:18px}
  .report-panel li::before{content:"";position:absolute;left:0;top:6px;width:6px;height:6px;background:var(--bullet)}
  .brand{font-family:"Bree Serif",Georgia,serif}
</style>
</head>
<body>
  <p class="lead">The Americans with Disabilities Act (ADA) is a comprehensive federal civil rights law prohibiting discrimination on the basis of disability, enforced by the Department of Justice (DOJ). The ADA prohibits discriminatory lack of access for individuals with disabilities to goods and services of public services and accommodations. Websites are considered places of public accommodations. The DOJ currently uses WCAG 2.1 Level A/AA as an accepted standard by which to measure a website’s accessibility.</p>

  <div class="standards-mark"><span class="square"></span><span class="name">K7P</span></div>

  <p class="scope">WCAG 2.1 Level A/AA consists of 13 guidelines with 50 checkpoints that are organized under four principles:</p>

  <section class="principle p1">
    <div class="tag">Principle <b>1</b></div>
    <h2>Perceivable</h2>
    <p>Information and user interface components must be presented to users in ways they can perceive. This means that users must be able to compre-hend the information being depicted:</p>
    <p class="key" style="margin-top:4px">It can’t be invisible to all their senses.</p>
  </section>

  <section class="principle p2">
    <div class="tag">Principle <b>2</b></div>
    <h2>Operable</h2>
    <p>User interface components and navigation must be operable:</p>
    <p class="key">The interface cannot require interaction that a user cannot perform.</p>
  </section>

  <section class="principle p3">
    <div class="tag">Principle <b>3</b></div>
    <h2>Understandable</h2>
    <p>Information and the operation of a user interface must be understandable:</p>
    <p class="key">Users must be able to understand the information as well as the operation of the user interface.</p>
  </section>

  <section class="principle p4">
    <div class="tag">Principle <b>4</b></div>
    <h2>Robust</h2>
    <p>Content must be robust enough that it can be interpreted reliably by a wide variety of user agents, including assistive technologies:</p>
    <p class="key">As technologies and user agents evolve, the content should remain accessible.</p>
  </section>

  <section class="report-panel">
    <p class="pitch">Start your journey to a fully compliant website with FlintVue™. This detailed compliance and remediation report is generated based on scanning your website against hundreds of carefully-crafted rules, logging failures, and then generating feedback and recommendations on how to fix the problems based on our years of experience and proven best practices.</p>
    <p class="overview">The FlintVue™ report is designed to be shared with your executive team and stakeholders. It is divided into two sections to build knowledge and self-sufficiency.</p>
    <ul>
      <li>The first section provides a detailed analysis of your website per the WCAG 2.1 A/AA principles and includes an at-a-glance Summary Chart for your executive team.</li>
      <li>The second section is designed specifically for your website development team, providing them with detailed examples of problematic issues, suggested ways to fix them, and links for more detailed training.</li>
    </ul>
  </section>
</body>
</html>
```